Camp Maplebrook 2018

We need a postcard design to advertise our summer programs. We are a Christian camp with day camp and overnight camps.

Target Market(s)

parents of elementary age kids

Industry/Entity Type

Christian

Colors
ec1f27
f37122
faa54b
fbee3d
f78f20
f04a50
fbed22
fbee3e

Requirements
Must have
• Day Camp 2018 "Shine Bright Daily"
• June 25 - August 24
• $135 per week
• Mon-Fri 8 am to 4 pm. Open to all kids entering grades 1 to 8. Day camp is chock full of activities like swimming, rock wall, archery, sports, crafts, air rifles and much more! Daily lunch and snack included. Before and after-care available at an extra rate.
• Register and pay in full by April 1st, save $270!
• Overnight Camp 2018
• July 15 - 21 & July 22 - 28
• $330 per week
• Open to all kids ages 8 to 14. Spend the week making new friends, sleeping in cabins, climbing the rock wall and swimming at the beach! Our guest speakers will lead twice daily chapel sessions that will challenge campers to grow in their faith.
• 42 Cedar Vale Rd. Barrington, NH 03819
• 603-418-5926
• www.maplebrook.org
Nice to have
• bright and colorful

```html
<!DOCTYPE html>
<html lang="en">
<head>
<meta charset="utf-8">
<title>Camp Maplebrook 2018 Postcard</title>
<link href="https://fonts.googleapis.com/css2?family=Oswald:wght@500;600;700&family=Jost:wght@400;500;600;700&family=Great+Vibes&display=swap" rel="stylesheet">
<style>
  :root {
    --red: #cc1f2f;
    --orange-red: #e2431d;
    --banner: #e04a1e;
    --brown: #6b3a1f;
    --ink: #1e1e1e;
    --blush: #fbe6ea;
    --white: #ffffff;
    --stage: #e7e5e2;
    --photo-warm-a: #b9a08a;
    --photo-warm-b: #7c6a5a;
    --photo-cool-a: #8f9a86;
    --photo-cool-b: #5f6f72;
  }
  * { box-sizing: border-box; margin: 0; padding: 0; }
  html, body { width: 1200px; height: 675px; overflow: hidden; }
  body {
    background: var(--stage);
    font-family: "Jost", sans-serif;
    color: var(--ink);
    position: relative;
  }
  .postcard {
    position: absolute;
    top: 138px;
    width: 530px;
    height: 398px;
    background: var(--white);
    overflow: hidden;
    box-shadow: 0 6px 18px rgba(0,0,0,0.18);
  }
  .postcard--front { left: 46px; }
  .postcard--back { left: 624px; }
  .card-art { position: absolute; inset: 0; width: 100%; height: 100%; }

  /* Front */
  .front-copy {
    position: absolute;
    right: 24px;
    top: 20px;
    width: 270px;
    text-align: right;
  }
  .front-title {
    font-family: "Oswald", sans-serif;
    font-weight: 600;
    font-size: 27px;
    line-height: 1;
    color: var(--red);
  }
  .tagline {
    font-family: "Great Vibes", cursive;
    font-size: 29px;
    line-height: 1;
    color: var(--brown);
    margin-top: 2px;
  }
  .date-banner {
    display: inline-block;
    background: var(--banner);
    color: var(--white);
    font-family: "Jost", sans-serif;
    font-weight: 500;
    font-size: 15px;
    line-height: 1.3;
    letter-spacing: 1.2px;
    padding: 1px 7px;
    margin-top: 4px;
  }
  .price {
    font-family: "Jost", sans-serif;
    font-weight: 700;
    font-size: 40px;
    line-height: 1;
    color: var(--red);
    margin-top: 6px;
  }
  .price-unit {
    font-family: "Oswald", sans-serif;
    font-weight: 500;
    font-size: 18px;
    line-height: 1;
    color: var(--brown);
    margin-top: 2px;
  }
  .front-body {
    font-size: 9.2px;
    line-height: 1.22;
    margin: 8px 0 0 auto;
    width: 205px;
  }
  .early-offer {
    font-family: "Oswald", sans-serif;
    font-weight: 500;
    font-size: 15px;
    line-height: 1;
    color: var(--ink);
    margin-top: 8px;
    letter-spacing: -0.2px;
  }
  .savings {
    font-family: "Jost", sans-serif;
    font-weight: 700;
    font-size: 35px;
    line-height: 1;
    color: var(--orange-red);
    margin-top: 2px;
  }
  .brand {
    position: absolute;
    right: 24px;
    bottom: 14px;
    display: flex;
    align-items: center;
    gap: 12px;
  }
  .brand-dot {
    width: 22px; height: 22px;
    border-radius: 50%;
    background: var(--red);
  }
  .brand-name {
    font-family: "Jost", sans-serif;
    font-weight: 600;
    font-size: 30px;
    line-height: 1;
    color: var(--red);
    text-align: right;
  }

  /* Back */
  .back-copy {
    position: absolute;
    left: 22px;
    top: 88px;
    width: 245px;
  }
  .back-title {
    font-family: "Oswald", sans-serif;
    font-weight: 700;
    font-size: 33px;
    line-height: 1;
    color: var(--red);
    text-shadow: 0 0 3px var(--white);
  }
  .back-copy .date-banner {
    font-family: "Oswald", sans-serif;
    font-size: 14px;
    letter-spacing: 0.4px;
    padding: 1px 6px;
    margin-top: 6px;
  }
  .back-copy .price { font-size: 36px; margin-top: 4px; }
  .back-body {
    font-size: 9px;
    line-height: 1.22;
    text-align: justify;
    margin-top: 6px;
    width: 235px;
  }
  .contact-row {
    display: flex;
    margin-top: 8px;
  }
  .contact-item { padding-right: 7px; }
  .contact-item + .contact-item {
    border-left: 1.5px solid var(--ink);
    padding-left: 7px;
  }
  .contact-label {
    font-family: "Oswald", sans-serif;
    font-weight: 600;
    font-size: 15px;
    line-height: 1.05;
    color: var(--ink);
  }
  .contact-value {
    font-family: "Oswald", sans-serif;
    font-weight: 600;
    font-size: 15px;
    line-height: 1.05;
    color: var(--red);
  }
</style>
</head>
<body>

<article class="postcard postcard--front">
  <svg class="card-art" viewBox="0 0 530 398">
    <defs>
      <linearGradient id="frontPhotoTone" x1="0" y1="0" x2="1" y2="1">
        <stop offset="0" stop-color="var(--photo-warm-a)"/>
        <stop offset="1" stop-color="var(--photo-warm-b)"/>
      </linearGradient>
    </defs>
    <path class="blush-sweep" fill="var(--blush)"
      d="M255,0 H300 C365,70 335,170 285,230 C245,280 265,340 370,398 H210 C185,320 195,230 245,170 C295,110 295,40 255,0 Z"/>
    <path class="photo-area" role="img" aria-label="Photo of a smiling young camper outdoors"
      fill="url(#frontPhotoTone)"
      d="M0,0 H255 C295,40 295,110 245,170 C195,230 185,320 210,398 H0 Z"/>
  </svg>

  <div class="front-copy">
    <h1 class="front-title">DAY CAMP 2018</h1>
    <p class="tagline">Shine Bright Daily</p>
    <p class="date-banner">JUNE 25 – AUGUST 24</p>
    <p class="price">$135</p>
    <p class="price-unit">PER WEEK</p>
    <p class="front-body">Mon-Fri 8 am to 4 pm. Open to kids entering grades 1 to 8. Day camp is chock full of activities like swimming, rock wall, archery, sports, crafts, air rifles and much more! Daily lunch and snack included. Before and after-care available at an extra rate.</p>
    <p class="early-offer">REGISTER &amp; PAY IN FULL BY APRIL 1ST</p>
    <p class="savings">SAVE $270</p>
  </div>

  <div class="brand">
    <span class="brand-dot"></span>
    <p class="brand-name">Camp<br>Maplebrook</p>
  </div>
</article>

<article class="postcard postcard--back">
  <svg class="card-art" viewBox="0 0 530 398">
    <defs>
      <linearGradient id="beachPhotoTone" x1="0" y1="0" x2="1" y2="1">
        <stop offset="0" stop-color="var(--photo-cool-a)"/>
        <stop offset="1" stop-color="#c9b29a"/>
      </linearGradient>
      <linearGradient id="lakePhotoTone" x1="0" y1="0" x2="0" y2="1">
        <stop offset="0" stop-color="#9aa58f"/>
        <stop offset="1" stop-color="var(--photo-cool-b)"/>
      </linearGradient>
    </defs>
    <circle class="photo-ring" cx="183" cy="52" r="80" fill="url(#beachPhotoTone)"
      stroke="var(--red)" stroke-width="5" role="img" aria-label="Photo of a smiling camper at the beach"/>
    <circle class="photo-ring" cx="218" cy="168" r="60" fill="url(#lakePhotoTone)"
      stroke="var(--red)" stroke-width="5" role="img" aria-label="Photo of a camper swimming in the lake"/>
    <path class="footer-wave" fill="var(--red)"
      d="M0,398 V370 C40,352 120,354 260,364 C380,372 480,380 530,364 V398 Z"/>
  </svg>

  <div class="back-copy">
    <h2 class="back-title">OVERNIGHT<br>CAMP 2018</h2>
    <p class="date-banner">JULY 15 - 21 &amp; JULY 22 - 28</p>
    <p class="price">$330</p>
    <p class="price-unit">PER WEEK</p>
    <p class="back-body">Open to kids ages 8 to 14. Spend the week making new friends, sleeping in cabins, climbing the rock wall and swimming at the beach! Our guest speakers will lead twice daily chapel sessions that will challenge campers to grow in their faith.</p>
    <div class="contact-row">
      <div class="contact-item">
        <p class="contact-label">CALL US</p>
        <p class="contact-value">603-418-5926</p>
      </div>
      <div class="contact-item">
        <p class="contact-label">VISIT US</p>
        <p class="contact-value">WWW.MAPLEBROOK.ORG</p>
      </div>
    </div>
  </div>
</article>

</body>
</html>
```